Build a landing page to promote a service (dialler consultation and support).

We are a call centre consultation firm and we need a landing page to promote a service. The service is Tormalux dialler consultation and support.
If you do not know what Tormalux is, please do some quick "Zorvex" research for more information.
The landing page will be promoted with a paid advertisement, so we want something that is simple, and explains exactly what service we offer.
There are two objectives for the landing page:
1) A "call to action" which directs the user to a contact page, including a form plus all of our contact details.
2) A form for them viewers to enter their details to get a "FREE" quote for their project. This form should be placed on the main page.
Notes:
The call to action will require the viewer to enter their name, email, phone number as well as a description of their request. There will also need to be a drop down menu for the type of quote. This menu should have the following options:
1) Tormalux support
2) Tormalux hosting
3) Tormalux customisation
4) Other
We need 2 pages in total:
1) Main landing page
This is the home page. It will need to clearly indicate our services and our key selling features.
Services:
* Tormalux support
* Tormalux hosting
* Tormalux customisation
Key Selling Features:
* Australian based
* PCI complaint
* 10+ years of dialler and call centre experience
* we run a sister company which is a highly reputable 40 seat call centre, so we know first hand about call centre technology.
The main landing page will have an "about us" section with a few paragraphs about how we got started.
-------------------------------------------------------------------------
2) Contact page
All of our contact details will live on this page, as well as a contact form.
Other notes:
We will be self hosting the landing page.
We already have a domain name.
The design must be clean and incorporate our logo, as well as it's colours. (Logo attached)
We want a fully function HTML landing page, not just a "PSD" design.
The page must be mobile optimised.
Anyone using Tormalux software.

```html
<!DOCTYPE html>
<html lang="en">
<head>
<meta charset="utf-8">
<title>Brightline – Tormalux Consultation &amp; Support</title>
<link href="https://fonts.googleapis.com/css2?family=Montserrat:wght@400;500;600;700&family=Arimo:wght@400;700&display=swap" rel="stylesheet">
<style>
:root{
  --blue:#1a7fc9;
  --blue-dark:#156fb4;
  --teal:#22ad8f;
  --teal-2:#2bb59a;
  --ink:#333;
  --footer:#2d2e31;
  --white:#fff;
}
*{box-sizing:border-box;margin:0;padding:0}
html,body{width:1200px;height:2744px;overflow:hidden}
body{position:relative;background:var(--white);font-family:"Arimo",Arial,sans-serif;color:var(--ink)}
.abs{position:absolute}
h1,h2,h3,h4{font-weight:400}

/* hero */
.hero-bg{left:0;top:0;width:1200px;height:760px}
.brand{left:86px;top:12px;display:flex;flex-direction:column;align-items:center;width:152px;gap:6px}
.brand-dot{width:58px;height:58px;border-radius:50%;background:var(--white)}
.brand-name{font-family:"Montserrat",sans-serif;font-weight:600;font-size:28px;color:var(--white);letter-spacing:.5px}
.nav a{position:absolute;top:56px;font-family:"Montserrat",sans-serif;font-weight:600;font-size:13px;color:var(--white);text-decoration:none;white-space:nowrap}
.nav-cta{left:961px;top:42px;width:152px;height:44px;border-radius:22px;background:var(--teal);color:var(--white);font-family:"Montserrat",sans-serif;font-weight:600;font-size:15px;display:flex;align-items:center;justify-content:center}
.hero-title{left:84px;top:212px;font-family:"Montserrat",sans-serif;font-weight:500;font-size:60px;line-height:1;color:var(--white)}
.hero-text{left:86px;top:292px;width:440px;font-size:12px;line-height:26px;color:var(--white)}
.field{left:86px;width:401px;background:var(--white);font-size:12.5px;color:#555;padding:0 15px;display:flex;align-items:center}
.field-area{align-items:flex-start;padding-top:14px}
.caret{margin-left:auto;width:0;height:0;border-left:5px solid transparent;border-right:5px solid transparent;border-top:5px solid #444}
.quote-btn{left:86px;top:643px;width:161px;height:43px;background:var(--teal);color:var(--white);font-family:"Montserrat",sans-serif;font-weight:600;font-size:12.5px;display:flex;align-items:center;justify-content:center}
.hero-ring{left:606px;top:158px;width:590px;height:590px;border-radius:50%;border:7px solid var(--teal-2);background:var(--white);padding:16px}
.photo{width:100%;height:100%;border-radius:50%;background:linear-gradient(160deg,#d9e3ea,#8fa2b6 55%,#4d5c70)}

/* services */
.section-title{font-family:"Montserrat",sans-serif;font-weight:400;font-size:36px;color:#333;text-align:center;width:1200px;left:0}
.section-sub{left:0;width:1200px;text-align:center;font-size:12.5px;color:#333}
.card{top:919px;width:318px;height:340px;background:var(--white);border-radius:6px;box-shadow:0 2px 10px rgba(0,0,0,.12);text-align:center}
.card-icon{position:absolute;left:103px;top:14px;width:112px;height:112px;border-radius:50%;border:4px solid var(--teal-2);padding:5px}
.card-icon span{display:flex;width:100%;height:100%;border-radius:50%;background:var(--blue);align-items:center;justify-content:center}
.card h3{position:absolute;top:150px;width:100%;font-family:"Montserrat",sans-serif;font-weight:600;font-size:16px;color:#222}
.card p{position:absolute;top:184px;left:22px;right:22px;font-size:12px;line-height:26px;color:#333}
.card-btn{position:absolute;left:107px;top:281px;width:104px;height:38px;border:1px solid var(--blue);color:var(--blue);font-family:"Montserrat",sans-serif;font-weight:600;font-size:12px;display:flex;align-items:center;justify-content:center}

/* features */
.features-bg{left:0;top:1320px;width:1200px;height:560px}
.feature-art{left:100px;top:1395px;width:430px;height:445px;border-radius:40px;background:radial-gradient(circle at 50% 50%,#f3c49a 0,#6fb7e3 45%,rgba(43,160,200,0) 72%)}
.features-title{left:611px;top:1440px;font-family:"Montserrat",sans-serif;font-weight:400;font-size:33px;color:var(--white)}
.features-text{left:614px;top:1500px;width:460px;font-size:12.5px;line-height:26px;color:var(--white)}
.features-list{left:616px;top:1605px;width:500px;list-style:none;font-size:12.5px;color:var(--white)}
.features-list li{display:flex;gap:14px;line-height:26px;margin-bottom:7.5px}
.features-list svg{flex:none;margin-top:8px}

/* about */
.about-title{left:86px;top:1932px;font-family:"Montserrat",sans-serif;font-weight:400;font-size:35px;color:#333}
.about-text{left:86px;top:1999px;width:480px;font-size:12px;line-height:28px;color:#333}
.about-text p+p{margin-top:28px}
.about-btn{left:86px;top:2250px;width:133px;height:46px;background:var(--blue);color:var(--white);font-family:"Montserrat",sans-serif;font-weight:600;font-size:13px;display:flex;align-items:center;justify-content:center}
.about-ring{left:682px;top:1913px;width:392px;height:392px;border-radius:50%;border:12px solid var(--teal-2);background:var(--white);padding:10px}
.about-ring .photo{background:linear-gradient(170deg,#e8e8e8,#b9bcc2 50%,#6d7077)}

/* footer */
.footer{left:0;top:2363px;width:1200px;height:381px;background:var(--footer);color:var(--white)}
.f-brand{left:115px;top:67px;width:260px;display:flex;flex-direction:column;align-items:center;gap:12px}
.f-brand-dot{width:112px;height:112px;border-radius:50%;background:var(--blue)}
.f-brand-name{font-family:"Montserrat",sans-serif;font-weight:600;font-size:46px;color:var(--blue)}
.f-head{top:38px;font-family:"Montserrat",sans-serif;font-weight:500;font-size:20px}
.f-contact{left:418px;top:92px;font-size:15px;line-height:19px}
.f-contact p{margin-bottom:18px}
.f-links{left:686px;top:94px;list-style:none;font-family:"Montserrat",sans-serif;font-size:12px;line-height:25.8px}
.f-input{left:850px;top:83px;width:263px;height:36px;background:var(--white);color:#333;font-family:"Montserrat",sans-serif;font-size:11px;font-weight:500;display:flex;align-items:center;padding-left:15px}
.f-sub{left:850px;top:131px;width:126px;height:36px;background:var(--blue);font-family:"Montserrat",sans-serif;font-size:14px;font-weight:500;display:flex;align-items:center;justify-content:center}
.f-social{left:849px;top:200px;display:flex;gap:5px}
.f-social span{width:38px;height:38px;border-radius:50%;border:1.5px solid var(--white);display:flex;align-items:center;justify-content:center}
.f-social span i{display:block;width:10px;height:10px;border-radius:50%;background:var(--white)}
.f-rule{left:86px;top:309px;width:1028px;height:1px;background:#45464a}
.f-copy{left:0;top:337px;width:1200px;text-align:center;font-size:12.5px}
</style>
</head>
<body>

<svg class="abs hero-bg" viewBox="0 0 1200 760" aria-hidden="true">
  <defs>
    <linearGradient id="heroGrad" x1="0" y1="0" x2="1" y2="1">
      <stop offset="0" stop-color="#1b7dc6"/>
      <stop offset="1" stop-color="#1766ad"/>
    </linearGradient>
  </defs>
  <path d="M0 0H1200V690C1050 740 880 760 700 760 450 760 220 720 0 735Z" fill="#22ad8f"/>
  <path d="M0 0H1200V680C1050 728 880 748 700 750 450 752 220 712 0 725Z" fill="url(#heroGrad)"/>
  <circle cx="160" cy="90" r="260" fill="none" stroke="#ffffff" stroke-opacity=".05" stroke-width="40"/>
</svg>

<div class="abs brand"><span class="brand-dot"></span><span class="brand-name">Brightline</span></div>
<nav class="nav">
  <a style="left:470px">HOME</a>
  <a style="left:564px">ABOUT US</a>
  <a style="left:683px">SERVICES</a>
  <a style="left:798px">NEWS</a>
  <a style="left:890px">CAREERS</a>
</nav>
<div class="abs nav-cta">CONTACT US</div>

<h1 class="abs hero-title">Brightline</h1>
<p class="abs hero-text">Sed ut perspiciatis unde omnis iste natus error sit voluptatem accusantium doloremque architecto beatae vitae dicta sunt explicabo.</p>

<div class="abs field" style="top:371px;height:40px">Name :</div>
<div class="abs field" style="top:415px;height:39px">Email :</div>
<div class="abs field" style="top:459px;height:39px">Phone :</div>
<div class="abs field" style="top:503px;height:40px">Select Service :<span class="caret"></span></div>
<div class="abs field field-area" style="top:548px;height:82px">Description of their Request :</div>
<div class="abs quote-btn">GET A FREE QUOTE</div>

<div class="abs hero-ring"><div class="photo" role="img" aria-label="Photo of a team of colleagues meeting around a laptop in a bright office"></div></div>

<h2 class="abs section-title" style="top:805px">OUR SERVICES</h2>
<p class="abs section-sub" style="top:864px">Sed ut perspiciatis unde omnis iste natus error sit voluptatem accusantium doloremque laudantium, totam rem aperiam</p>

<div class="abs card" style="left:86px">
  <div class="card-icon"><span>
    <svg width="56" height="56" viewBox="0 0 56 56" fill="none" stroke="#fff" stroke-width="2"><circle cx="28" cy="28" r="14"/><path d="M12 28a16 16 0 0 1 32 0"/><rect x="9" y="26" width="6" height="10" rx="2"/><rect x="41" y="26" width="6" height="10" rx="2"/><path d="M44 36c0 6-5 9-12 9"/></svg>
  </span></div>
  <h3>TORMALUX SUPPORT</h3>
  <p>Sed ut perspiciatis unde omnis iste natus error sit voluptatem accusantium doloremque laudantium, totam rem aperiam eaque ipsa</p>
  <div class="card-btn">READ MORE</div>
</div>
<div class="abs card" style="left:441px">
  <div class="card-icon"><span>
    <svg width="56" height="56" viewBox="0 0 56 56" fill="none" stroke="#fff" stroke-width="2"><rect x="14" y="8" width="28" height="10" rx="4"/><rect x="14" y="21" width="28" height="10" rx="4"/><rect x="14" y="34" width="28" height="10" rx="4"/><path d="M28 44v4M10 48h36"/><circle cx="10" cy="48" r="2"/><circle cx="46" cy="48" r="2"/></svg>
  </span></div>
  <h3>TORMALUX HOSTING</h3>
  <p>Sed ut perspiciatis unde omnis iste natus error sit voluptatem accusantium doloremque laudantium, totam rem aperiam eaque ipsa</p>
  <div class="card-btn">READ MORE</div>
</div>
<div class="abs card" style="left:796px">
  <div class="card-icon"><span>
    <svg width="56" height="56" viewBox="0 0 56 56" fill="none" stroke="#fff" stroke-width="2"><rect x="8" y="8" width="32" height="32"/><rect x="14" y="14" width="34" height="34"/><circle cx="32" cy="32" r="6"/><path d="M32 22v4M32 38v4M22 32h4M38 32h4"/></svg>
  </span></div>
  <h3>TORMALUX CUSTOMISATION</h3>
  <p>Sed ut perspiciatis unde omnis iste natus error sit voluptatem accusantium doloremque laudantium, totam rem aperiam eaque ipsa</p>
  <div class="card-btn">READ MORE</div>
</div>

<svg class="abs features-bg" viewBox="0 0 1200 560" aria-hidden="true">
  <defs>
    <linearGradient id="featGrad" x1="0" y1="0" x2="1" y2="0">
      <stop offset="0" stop-color="#22ad8f"/>
      <stop offset="1" stop-color="#1b7cc6"/>
    </linearGradient>
  </defs>
  <path d="M0 90C300 20 700 -10 1200 100V450C900 540 500 580 0 450Z" fill="url(#featGrad)"/>
</svg>
<div class="abs feature-art" role="img" aria-label="Illustration of a hand holding a phone with a support agent, surrounded by 24h customer service icons"></div>
<h2 class="abs features-title">OUR FEATURES</h2>
<p class="abs features-text">Sed ut perspiciatis unde omnis iste natus error sit voluptatem accusantium doloremque laudantium, totam rem aperiam, eaque ipsa quae ab illo inventore veritatis et quasi architecto beatae vitae dicta sunt explicabo.</p>
<ul class="abs features-list">
  <li><svg width="12" height="10" viewBox="0 0 12 10"><path d="M1 5l3.5 3.5L11 1" fill="none" stroke="#fff" stroke-width="2"/></svg>Australian based</li>
  <li><svg width="12" height="10" viewBox="0 0 12 10"><path d="M1 5l3.5 3.5L11 1" fill="none" stroke="#fff" stroke-width="2"/></svg>PCI compliant</li>
  <li><svg width="12" height="10" viewBox="0 0 12 10"><path d="M1 5l3.5 3.5L11 1" fill="none" stroke="#fff" stroke-width="2"/></svg>10+ years of dialler and call centre experience</li>
  <li><svg width="12" height="10" viewBox="0 0 12 10"><path d="M1 5l3.5 3.5L11 1" fill="none" stroke="#fff" stroke-width="2"/></svg>we run a sister company which is a highly reputable 40 seat call centre, so we know first hand about call centre technology.</li>
</ul>

<h2 class="abs about-title">ABOUT OUR COMPANY</h2>
<div class="abs about-text">
  <p>Sed ut perspiciatis unde omnis iste natus error sit voluptatem accusantium doloremque laudantium, totam rem aperiam, eaque ipsa quae ab illo inventore veritatis et quasi architecto beatae vitae dicta sunt explicabo. Nemo enim ipsam voluptatem quia voluptas sit magni dolores eos qui ratione voluptatem sequi nesciunt.</p>
  <p>Neque porro quisquam est, qui dolorem ipsum quia dolor sit amet, consectetur, adipisci velit, sed quia non numquam eius modi tempora incidunt ut labore et dolore magnam aliquam quaerat voluptatem. Ut enim ad minima</p>
</div>
<div class="abs about-btn">READ MORE</div>
<div class="abs about-ring"><div class="photo" role="img" aria-label="Photo of a call centre supervisor with a headset and tablet standing among agents at their desks"></div></div>

<footer class="abs footer">
  <div class="abs f-brand"><span class="f-brand-dot"></span><span class="f-brand-name">Brightline</span></div>

  <h4 class="abs f-head" style="left:418px">CONTACT US</h4>
  <div class="abs f-contact">
    <p>ADDRESS<br>No.27,Sample Street Demo Town<br>Placeholder</p>
    <p>PHONE<br>000-555-0199</p>
    <p>EMAIL<br>info@brightline-demo.com/</p>
  </div>

  <h4 class="abs f-head" style="left:680px">COMPANY</h4>
  <ul class="abs f-links"><li>HOME</li><li>ABOUT US</li><li>SERVICES</li><li>NEWS</li><li>CAREERS</li><li>CONTACT US</li></ul>

  <h4 class="abs f-head" style="left:848px">KEEP IN TOUCH</h4>
  <div class="abs f-input">EMAIL ADDRESS</div>
  <div class="abs f-sub">SUBSCRIBE</div>
  <div class="abs f-social" aria-label="Social links"><span><i></i></span><span><i></i></span><span><i></i></span><span><i></i></span><span><i></i></span></div>

  <div class="abs f-rule"></div>
  <p class="abs f-copy">© Copyright 2018 Brightline.All rightt reserved.</p>
</footer>

</body>
</html>
```